Water ATM Card

Need a design for water ATM cards. Size of card is 3.375 x 2.125 inch
On the Front include the Cedar hollow Logo.
Bottom right corner should have Price $100
On the Back
This card is to be used to access water refills at any Cedar Hollow Water Vending Machines.
Please contact (869) 418 2930 or (869) 534 1276 or email clearflowbox@mailvista.example for any assistance or recharging of card.

```html
<!DOCTYPE html>
<html lang="en">
<head>
<meta charset="utf-8">
<title>Cedar Hollow Water Card</title>
<link href="https://fonts.googleapis.com/css2?family=Montserrat:wght@400;500;700;800&display=swap" rel="stylesheet">
<style>
  :root {
    --stage: #1d1d1d;
    --card-white: #ffffff;
    --brand-blue: #2a5fb0;
    --name-blue: #26479a;
    --ink: #1a1a1a;
    --accent-green: #3aa844;
    --back-top: #2f7fbf;
    --back-bottom: #2e3a88;
    --back-text: #e9eefa;
    --faint-name: rgba(30, 50, 120, 0.55);
  }
  * { box-sizing: border-box; margin: 0; padding: 0; }
  html, body {
    width: 1200px; height: 1059px; overflow: hidden;
    background: var(--stage);
    font-family: "Montserrat", sans-serif;
  }
  .canvas { position: relative; width: 1200px; height: 1059px; }
  .card { position: absolute; border-radius: 24px; overflow: hidden; }

  .card-front {
    left: 256px; top: 87px; width: 688px; height: 393px;
    background: var(--card-white);
  }
  .brand-name {
    position: absolute; left: 38px; top: 48px;
    font-weight: 800; font-size: 26px; letter-spacing: 0.5px;
    color: var(--brand-blue); text-transform: uppercase;
  }
  .holder { position: absolute; right: 44px; top: 44px; text-align: right; }
  .holder-name {
    font-weight: 800; font-size: 23px; color: var(--name-blue);
    letter-spacing: 0.4px; line-height: 28px;
  }
  .holder-role { font-weight: 500; font-size: 14px; color: var(--ink); margin-top: 4px; letter-spacing: 0.5px; }
  .accent-bar {
    position: absolute; right: 0; top: 45px; width: 28px; height: 46px;
    background: var(--accent-green);
  }
  .address {
    position: absolute; left: 38px; top: 182px;
    font-size: 16px; line-height: 18px; color: var(--ink);
  }
  .contacts { position: absolute; left: 37px; top: 251px; list-style: none; }
  .contacts li {
    display: flex; align-items: center; gap: 7px;
    font-size: 16px; color: var(--ink); height: 24px;
  }
  .contacts li:nth-child(1) { margin-bottom: 4px; }
  .contacts svg { width: 15px; height: 15px; fill: var(--brand-blue); flex: none; }
  .price {
    position: absolute; right: 36px; top: 204px;
    font-weight: 800; font-size: 22px; color: var(--accent-green);
  }

  .card-back {
    left: 253px; top: 546px; width: 695px; height: 395px;
    background: linear-gradient(160deg, var(--back-top) 0%, #3a5aa0 45%, var(--back-bottom) 100%);
  }
  .back-name {
    position: absolute; left: 0; right: 0; top: 208px; text-align: center;
    font-weight: 800; font-size: 40px; letter-spacing: 1px;
    color: var(--faint-name); text-transform: uppercase;
  }
  .back-note {
    position: absolute; left: 0; right: 0; bottom: 36px; text-align: center;
    font-size: 14px; line-height: 19px; color: var(--back-text); letter-spacing: 0.3px;
  }
</style>
</head>
<body>
<main class="canvas">
  <section class="card card-front">
    <div class="brand-name">Cedar Hollow</div>
    <div class="holder">
      <div class="holder-name">DANA WHITLOW</div>
      <div class="holder-role">OWNER</div>
    </div>
    <div class="accent-bar"></div>
    <p class="address">4810 Ridgeway Lane, Ste<br>210 Brookfield, TN37912</p>
    <ul class="contacts">
      <li>
        <svg viewBox="0 0 24 24"><path d="M6.6 10.8a15 15 0 0 0 6.6 6.6l2.2-2.2a1 1 0 0 1 1-.25 11.4 11.4 0 0 0 3.6.57 1 1 0 0 1 1 1V20a1 1 0 0 1-1 1A17 17 0 0 1 3 4a1 1 0 0 1 1-1h3.5a1 1 0 0 1 1 1c0 1.25.2 2.45.57 3.6a1 1 0 0 1-.25 1z"/></svg>
        (869) 418 2930
      </li>
      <li>
        <svg viewBox="0 0 24 24"><path d="M7 1h10a2 2 0 0 1 2 2v18a2 2 0 0 1-2 2H7a2 2 0 0 1-2-2V3a2 2 0 0 1 2-2zm0 3v14h10V4zm5 15.2a1.2 1.2 0 1 0 0 2.4 1.2 1.2 0 0 0 0-2.4z"/></svg>
        (869) 534 1276
      </li>
      <li>
        <svg viewBox="0 0 24 24"><path d="M2 5h20v14H2zm2 2v.5l8 5 8-5V7z"/></svg>
        clearflowbox@mailvista.example
      </li>
      <li>
        <svg viewBox="0 0 24 24"><path d="M12 2a10 10 0 1 0 0 20 10 10 0 0 0 0-20zm-1 17.9A8 8 0 0 1 4.2 10L9 15v1a2 2 0 0 0 2 2zm6.9-2.5A2 2 0 0 0 16 16h-1v-3a1 1 0 0 0-1-1H8v-2h2a1 1 0 0 0 1-1V7h2a2 2 0 0 0 2-2v-.4a8 8 0 0 1 2.9 12.8z"/></svg>
        www.cedarhollowwater.example
      </li>
    </ul>
    <div class="price">Price $100</div>
  </section>

  <section class="card card-back">
    <div class="back-name">Cedar Hollow</div>
    <p class="back-note">This card is to be used to access water refills at any<br>Cedar Hollow Water Vending Machines. Please contact<br>(869) 418 2930 or (869) 534 1276 or email clearflowbox@mailvista.example<br>for any assistance or recharging of card.</p>
  </section>
</main>
</body>
</html>
```